Maple9Tone

I need a website designed to feature a new product for my company. I am dedicating a separate site just highlight the program. The url will be maple9tone.com and the product name is maple tone. The product is ringless voicemail. We take a recorded script and send it to our clients customers cell phones without the phone ringing.

The site will consist of a home page. I animated video demo. It will house 18 scripts and voice overs to match, a results page, and a page to request a live demo.

We sell the product to new car dealerships

```html
<!DOCTYPE html>
<html lang="en">
<head>
<meta charset="utf-8">
<title>Maple9Tone – Ringless Voicemail</title>
<link href="https://fonts.googleapis.com/css2?family=Roboto:ital,wght@0,300;0,400;0,500;0,700;1,400&display=swap" rel="stylesheet">
<style>
:root{
  --blue:#0ea4dc;
  --blue-dark:#0b8ec0;
  --ink:#222;
  --text:#777;
  --light:#f3f5f7;
  --gray:#ececec;
  --footer:#3c3c3c;
  --jan:#8a3cb0;
  --feb:#6c46c2;
  --mar:#3d8fe0;
  --apr:#1bb4c6;
}
*{box-sizing:border-box;margin:0;padding:0}
html,body{width:1200px;height:3636px;overflow:hidden}
body{font-family:'Roboto',sans-serif;color:var(--text);background:#fff;position:relative}
section,header,footer{position:absolute;left:0;width:1200px}
.abs{position:absolute}
.section-title{color:var(--blue);font-size:22px;font-weight:500;text-align:center;text-transform:uppercase;width:100%}
.section-lead{font-size:13px;line-height:24px;text-align:center;width:680px;left:260px}

/* header */
.site-header{top:0;height:87px;background:#fff}
.brand{left:85px;top:28px;font-size:28px;font-weight:700;color:var(--ink)}
.main-nav{right:150px;top:36px;display:flex;gap:44px;font-size:13px;font-weight:500;color:#333}
.main-nav .active{color:var(--blue)}
.search-btn{left:1068px;top:21px;width:46px;height:46px;border:2px solid var(--blue);border-radius:50%}

/* hero */
.hero{top:87px;height:483px;background:linear-gradient(100deg,#3a2a22 0%,#7a5a44 35%,#a58a72 60%,#5b4638 100%)}
.hero-title{left:106px;top:155px;color:#fff;font-size:32px;font-weight:700}
.hero-text{left:106px;top:213px;width:440px;color:#fff;font-size:13px;line-height:22px}
.hero-btn{left:106px;top:306px;width:146px;height:40px;border:2px solid #fff;color:#fff;font-size:13px;font-weight:500;text-align:center;line-height:36px}
.slider-arrow{top:216px;width:54px;height:54px;border:2px solid #fff;border-radius:50%}
.slider-arrow svg{position:absolute;left:16px;top:15px}

/* how it works */
.how{top:570px;height:630px;background:#fff}
.step-caption{width:200px;font-size:11.5px;line-height:19px;text-align:center;color:#888}

/* offer */
.offer{top:1200px;height:436px;background:var(--light)}
.phone{width:172px;height:356px;border:3px solid #c8c8c8;border-radius:28px;background:#fff}
.phone-screen{position:absolute;left:10px;top:38px;width:146px;height:244px;border:1px solid #ddd}
.phone-home{position:absolute;left:69px;bottom:14px;width:30px;height:30px;border:2px solid #bbb;border-radius:50%}
.offer-title{left:450px;top:102px;width:300px;text-align:center;font-size:26px;font-weight:500;color:var(--blue)}
.offer-list{left:450px;width:330px;font-size:12.5px;line-height:20px;list-style:none}
.offer-list li{position:absolute;left:0;padding-left:36px;width:330px}
.offer-list li::before{content:"";position:absolute;left:0;top:4px;width:12px;height:12px;border:3px solid var(--blue);border-radius:50%}

/* video */
.video{top:1636px;height:412px;background:#fff}
.video-title{left:85px;top:55px;color:var(--blue);font-size:22px;font-weight:500}
.video-copy{left:85px;width:480px;font-size:13px;line-height:24px}
.btn-solid{background:var(--blue);color:#fff;font-size:13px;font-weight:500;text-align:center}
.video-art{left:613px;top:50px;width:502px;height:308px;background:linear-gradient(135deg,#2ea8dd,#1b86c4)}

/* testimonial */
.testimonial{top:2048px;height:218px;background:var(--blue)}
.avatar{left:129px;top:47px;width:124px;height:124px;border-radius:50%;border:5px solid #fff;background:linear-gradient(160deg,#c8b7a6,#7d6a5c)}
.quote-rule{left:291px;top:42px;width:1px;height:134px;background:rgba(255,255,255,.6)}
.quote{left:322px;top:44px;width:760px;color:#fff;font-size:14px;font-style:italic;line-height:28px}
.quote-author{left:322px;top:146px;color:#fff;font-size:14px;font-weight:700;text-transform:uppercase}

/* scripts */
.scripts{top:2266px;height:424px;background:var(--gray)}
.script-card{top:168px;width:225px;height:210px}
.script-ribbon{position:absolute;left:0;top:0;width:225px;height:62px}
.script-month{position:absolute;left:26px;top:14px;color:#fff;font-size:23px;font-weight:700}
.script-num{position:absolute;right:14px;top:8px;width:46px;height:46px;border-radius:50%;background:#fff;text-align:center;line-height:46px;font-size:20px;font-weight:700}
.script-body{position:absolute;left:26px;top:72px;width:173px;height:128px;color:#fff;font-size:18px;font-weight:500;text-align:center;line-height:30px;padding-top:34px;text-transform:uppercase;box-shadow:0 0 0 10px rgba(255,255,255,.85)}
.carousel-arrow{top:290px}

/* references */
.references{top:2690px;height:316px;background:#fff}
.ref-box{top:170px;height:102px;border:1px solid #e2e2e2;border-radius:4px;display:flex;align-items:center;justify-content:center;font-size:22px;font-weight:700;color:#555;text-transform:uppercase;letter-spacing:1px}

/* stats band */
.stats{top:3006px;height:72px;background:var(--blue);display:flex;justify-content:space-around;align-items:center;padding:0 30px;color:#fff;font-size:16px;font-weight:700}
.stats span{display:flex;align-items:center;gap:10px}
.stats i{width:14px;height:14px;border:3px solid #fff;border-radius:50%;display:inline-block}

/* subscribe + contact */
.contact{top:3078px;height:498px;background:linear-gradient(120deg,#f1f0ec,#e7ebe6 60%,#eef0f2)}
.subscribe-card{left:97px;top:42px;width:465px;height:395px;background:var(--blue);color:#fff}
.sub-mark{position:absolute;left:38px;top:36px;width:56px;height:56px;border-radius:50%;border:4px solid #fff}
.sub-title{position:absolute;left:136px;top:34px;font-size:22px;font-weight:500}
.sub-text{position:absolute;left:136px;top:66px;width:300px;font-size:14px;line-height:22px}
.field{position:absolute;height:40px;border-bottom:1px solid rgba(255,255,255,.85);font-size:14px;padding-top:14px}
.signup{position:absolute;left:40px;top:325px;width:122px;height:42px;background:#fff;color:var(--blue);font-size:14px;font-weight:700;text-align:center;line-height:42px}
.privacy{position:absolute;left:184px;top:338px;font-size:13px}
.contact-brand{left:604px;top:50px;color:var(--blue);font-size:32px;font-weight:500}
.contact-q{left:604px;top:130px;color:var(--ink);font-size:21px;font-weight:500}
.contact-text{left:604px;top:174px;width:500px;font-size:13px;line-height:24px;color:#555}
.contact-row{left:604px;display:flex;align-items:center;gap:18px;font-size:18px;color:#333}
.contact-icon{width:44px;height:44px;border:2px solid var(--blue);border-radius:50%;display:flex;align-items:center;justify-content:center}

/* footer */
.site-footer{top:3576px;height:60px;background:var(--footer);color:#ccc;font-size:12px}
.copyright{left:85px;top:23px}
.social{right:82px;top:12px;display:flex;gap:10px}
.social i{width:36px;height:36px;border:1px solid #bbb;border-radius:50%;display:block}
</style>
</head>
<body>

<header class="site-header">
  <div class="abs brand">MAPLE9TONE</div>
  <nav class="abs main-nav">
    <span class="active">HOME</span><span>HOW IT WORKS</span><span>RESULTS</span><span>CONTACT US</span><span>ABOUT US</span><span>BLOG</span>
  </nav>
  <div class="abs search-btn">
    <svg width="46" height="46" viewBox="0 0 46 46"><circle cx="21" cy="21" r="6" fill="none" stroke="#0ea4dc" stroke-width="2.5"/><line x1="25.5" y1="25.5" x2="30" y2="30" stroke="#0ea4dc" stroke-width="2.5"/></svg>
  </div>
</header>

<section class="hero" role="img" aria-label="Photo of a young woman reading a message on her smartphone in a warm city street">
  <div class="abs hero-title">MAPLE9TONE</div>
  <p class="abs hero-text">Sed ut perspiciatis unde omnis iste natus error sit voluptatem accusantium doloremque laudantium, totam rem aperiam, inventore veritatis et quasi architecto beatae vitae dicta sunt explicabo.</p>
  <div class="abs hero-btn">READ MORE</div>
  <div class="abs slider-arrow" style="left:24px"><svg width="20" height="20" viewBox="0 0 20 20"><path d="M13 3 6 10l7 7" fill="none" stroke="#fff" stroke-width="3"/></svg></div>
  <div class="abs slider-arrow" style="left:1122px"><svg width="20" height="20" viewBox="0 0 20 20"><path d="M7 3l7 7-7 7" fill="none" stroke="#fff" stroke-width="3"/></svg></div>
</section>

<section class="how">
  <h2 class="abs section-title" style="top:43px">How it works</h2>
  <p class="abs section-lead" style="top:74px">Sed ut perspiciatis unde omnis iste natus error sit voluptatem accusantium doloremque laudantium, totam rem aperiam, inventore veritatis et quasi architecto beatae vitae dicta sunt explicabo.</p>

  <svg class="abs" style="left:0;top:0" width="1200" height="630" viewBox="0 0 1200 630">
    <defs>
      <marker id="arrowhead" markerWidth="8" markerHeight="8" refX="7" refY="4" orient="auto"><path d="M0 0 8 4 0 8" fill="none" stroke="#bbb" stroke-width="1.2"/></marker>
    </defs>
    <g stroke="#ccc" stroke-width="1.5" fill="none" marker-end="url(#arrowhead)">
      <line x1="200" y1="330" x2="300" y2="250"/>
      <line x1="430" y1="225" x2="535" y2="225"/>
      <line x1="672" y1="225" x2="775" y2="225"/>
      <line x1="910" y1="245" x2="1000" y2="320"/>
      <line x1="1000" y1="425" x2="905" y2="470"/>
      <line x1="785" y1="477" x2="675" y2="477"/>
      <line x1="540" y1="477" x2="430" y2="477"/>
      <line x1="305" y1="460" x2="210" y2="410"/>
    </g>
    <g fill="#0ea4dc" stroke="#fff" stroke-width="4">
      <circle cx="364" cy="225" r="55" stroke="#d6eef8" stroke-width="6"/>
      <circle cx="606" cy="225" r="55" stroke="#d6eef8" stroke-width="6"/>
      <circle cx="844" cy="225" r="55" stroke="#d6eef8" stroke-width="6"/>
      <circle cx="364" cy="477" r="55" stroke="#d6eef8" stroke-width="6"/>
      <circle cx="606" cy="477" r="55" stroke="#d6eef8" stroke-width="6"/>
      <circle cx="844" cy="477" r="55" stroke="#d6eef8" stroke-width="6"/>
      <circle cx="1047" cy="370" r="62" stroke="#0ea4dc" stroke-width="4"/>
    </g>
    <circle cx="153" cy="375" r="62" fill="#444" stroke="#0ea4dc" stroke-width="5"/>
    <circle cx="1047" cy="370" r="56" fill="#0ea4dc" stroke="#fff" stroke-width="4"/>
    <g fill="none" stroke="#fff" stroke-width="3">
      <!-- phone -->
      <rect x="352" y="203" width="24" height="42" rx="4"/><line x1="360" y1="239" x2="368" y2="239"/>
      <!-- team -->
      <circle cx="606" cy="212" r="6" fill="#fff"/><circle cx="591" cy="218" r="5" fill="#fff"/><circle cx="621" cy="218" r="5" fill="#fff"/>
      <path d="M594 240q12-20 24 0z" fill="#fff"/><path d="M580 240q8-14 16-4M632 240q-8-14-16-4" fill="#fff"/>
      <!-- laptop -->
      <rect x="828" y="208" width="32" height="22" rx="2"/><line x1="820" y1="237" x2="868" y2="237"/>
      <!-- voicemail -->
      <circle cx="136" cy="375" r="11"/><circle cx="170" cy="375" r="11"/><line x1="136" y1="386" x2="170" y2="386"/>
      <!-- mailbox -->
      <path d="M1025 392v-30q0-12 14-12h22q12 0 12 12v30z" fill="#fff"/><line x1="1047" y1="392" x2="1047" y2="405"/><rect x="1050" y="340" width="3" height="16" fill="#fff"/>
      <!-- share -->
      <circle cx="354" cy="477" r="5" fill="#fff"/><circle cx="374" cy="465" r="5" fill="#fff"/><circle cx="374" cy="489" r="5" fill="#fff"/><path d="M354 477l20-12M354 477l20 12"/>
      <!-- search -->
      <circle cx="602" cy="473" r="11"/><line x1="610" y1="481" x2="620" y2="491"/>
      <!-- envelope -->
      <rect x="826" y="464" width="36" height="26" rx="2"/><path d="M826 466l18 13 18-13"/>
    </g>
  </svg>

  <p class="abs step-caption" style="left:264px;top:290px">We develop and record a script based on your stores current needs, incentives</p>
  <p class="abs step-caption" style="left:506px;top:290px">Your team will be coached and given a set of scripted responses to be sure everyone</p>
  <p class="abs step-caption" style="left:744px;top:290px">Your message and list are uploaded to our system and delivered at any speed you wish</p>
  <p class="abs step-caption" style="left:53px;top:456px">We select a targeted list of past sales customers, service customers, or unsold leads</p>
  <p class="abs step-caption" style="left:947px;top:450px">Every inbound phone call is recorded, tracked, and caller information is captured</p>
  <p class="abs step-caption" style="left:264px;top:548px">Inbound return calls will begin within minutes</p>
  <p class="abs step-caption" style="left:506px;top:548px">This program requires zero set up</p>
  <p class="abs step-caption" style="left:744px;top:548px">The simple process above can be completed and go live in as little as 24 hours</p>
</section>

<section class="offer">
  <svg class="abs" style="left:0;top:0" width="1200" height="436" viewBox="0 0 1200 436">
    <path d="M335 150Q600 -10 865 150" fill="none" stroke="#9aa" stroke-width="2" stroke-dasharray="3 7"/>
  </svg>
  <div class="abs phone" style="left:156px;top:40px">
    <div class="phone-screen" role="img" aria-label="Illustration of blue speech bubbles with a voicemail symbol" style="background:linear-gradient(#fff,#eef8fd)"></div>
    <div class="phone-home"></div>
  </div>
  <div class="abs phone" style="left:873px;top:40px">
    <div class="phone-screen" style="padding:10px;font-size:10.5px;line-height:18px;color:#333;overflow:hidden">Hi this is (Managers Name), I'm the (Title) at Dealership). I have a customer that's interested in a car like the one you purchased from us and I'm hoping you would be interested in allowing us to buy it back from you? I'd be willing to pay you up to 120% of Valley Price Guide for that vehicle.</div>
    <div class="phone-home"></div>
  </div>
  <h2 class="abs offer-title">THE OFFER</h2>
  <ul class="abs offer-list" style="top:0">
    <li style="top:182px">We can use this as a buy back offer, re-engage unsold CRM leads, offer monthly factory incentives, inform of a sales event, or to get CSI surveys completed</li>
    <li style="top:266px">It can be recorded by anyone!</li>
    <li style="top:303px">Works because the message is perfect every time!</li>
    <li style="top:344px">The information stays with them!</li>
  </ul>
</section>

<section class="video">
  <h2 class="abs video-title">OUR VIDEO</h2>
  <p class="abs video-copy" style="top:95px">Sed ut perspiciatis unde omnis iste natus error sit voluptatem accusantium doloremque laudantium, totam rem aperiam, eaque ipsa quae ab illo inventore veritatis et quasi architecto beatae vitae dicta sunt explicabo. Nemo enim ipsam sed quia consequuntur magni dolores eos qui ratione voluptatem sequi nesciunt.</p>
  <p class="abs video-copy" style="top:210px">Sed ut perspiciatis unde omnis iste natus error sit voluptatem accusantium doloremque laudantium, totam rem aperiam, eaque ipsa quae ab illo inventore veritatis et quasi architecto beatae vitae dicta sunt explicabo. Nemo enim ipsam sed quia consequuntur magni dolores eos qui ratione voluptatem sequi nesciunt.</p>
  <div class="abs btn-solid" style="left:85px;top:325px;width:142px;height:40px;line-height:40px">WATCH VIDEO</div>
  <div class="abs video-art" role="img" aria-label="Illustration of a tablet sending red voicemail envelopes, with a play button"></div>
</section>

<section class="testimonial">
  <div class="abs avatar" role="img" aria-label="Portrait photo of the dealer giving the testimonial"></div>
  <div class="abs quote-rule"></div>
  <p class="abs quote">I have used Maple9Tone to my sales and service database as well as to unsold leads. I have been surprised that the results are as advertised. We get a steady stream of traffic from these messages and I have incorporated this program into all of my stores monthly budget</p>
  <div class="abs quote-author">Dale R IL Norvale Dealer</div>
</section>

<section class="scripts">
  <h2 class="abs section-title" style="top:40px">Available Scripts</h2>
  <p class="abs section-lead" style="top:73px">Sed ut perspiciatis unde omnis iste natus error sit voluptatem accusantium doloremque laudantium, totam rem aperiam, inventore veritatis et quasi architecto beatae vitae dicta sunt explicabo.</p>

  <svg class="abs carousel-arrow" style="left:30px" width="24" height="44" viewBox="0 0 24 44"><path d="M22 2 2 22l20 20" fill="none" stroke="#333" stroke-width="2"/></svg>
  <svg class="abs carousel-arrow" style="left:1146px" width="24" height="44" viewBox="0 0 24 44"><path d="M2 2l20 20-20 20" fill="none" stroke="#333" stroke-width="2"/></svg>

  <div class="abs script-card" style="left:88px">
    <svg class="script-ribbon" viewBox="0 0 225 62"><path d="M0 6h225v50H0l14-25z" fill="var(--jan)"/></svg>
    <span class="script-month">January</span><span class="script-num" style="color:var(--jan)">01</span>
    <div class="script-body" style="background:var(--jan)">New<br>Years</div>
  </div>
  <div class="abs script-card" style="left:348px">
    <svg class="script-ribbon" viewBox="0 0 225 62"><path d="M0 6h225v50H0l14-25z" fill="var(--feb)"/></svg>
    <span class="script-month">February</span><span class="script-num" style="color:var(--feb)">02</span>
    <div class="script-body" style="background:var(--feb)">Winter<br>Special</div>
  </div>
  <div class="abs script-card" style="left:616px">
    <svg class="script-ribbon" viewBox="0 0 225 62"><path d="M0 6h225v50H0l14-25z" fill="var(--mar)"/></svg>
    <span class="script-month">March</span><span class="script-num" style="color:var(--mar)">03</span>
    <div class="script-body" style="background:var(--mar)">Spring<br>Forward</div>
  </div>
  <div class="abs script-card" style="left:877px">
    <svg class="script-ribbon" viewBox="0 0 225 62"><path d="M0 6h225v50H0l14-25z" fill="var(--apr)"/></svg>
    <span class="script-month">April</span><span class="script-num" style="color:var(--apr)">04</span>
    <div class="script-body" style="background:var(--apr)">Tax<br>Time</div>
  </div>
</section>

<section class="references">
  <h2 class="abs section-title" style="top:40px">Our References</h2>
  <p class="abs section-lead" style="top:73px">Sed ut perspiciatis unde omnis iste natus error sit voluptatem accusantium doloremque laudantium, totam rem aperiam, inventore veritatis et quasi architecto beatae vitae dicta sunt explicabo.</p>
  <div class="abs ref-box" style="left:97px;width:189px">Norvale</div>
  <div class="abs ref-box" style="left:305px;width:182px">Crestline</div>
  <div class="abs ref-box" style="left:511px;width:185px">Dunmore</div>
  <div class="abs ref-box" style="left:718px;width:181px">Fairholt</div>
  <div class="abs ref-box" style="left:923px;width:180px">Brightway</div>
</section>

<section class="stats">
  <span><i></i>Illinois Norvale Dealer- 241 inbound calls</span>
  <span><i></i>South Carolina Fairholt Dealer- 363 inbound calls</span>
  <span><i></i>Texas CDBL Dealer- 361 inbound calls</span>
</section>

<section class="contact" role="img" aria-label="Faint map of the United States behind the contact area">
  <div class="abs subscribe-card">
    <div class="sub-mark"></div>
    <div class="sub-title">SUBSCRIBE</div>
    <p class="sub-text">Sign up with your email address to receive the latest news and updates.</p>
    <div class="field" style="left:40px;top:145px;width:175px">First Name</div>
    <div class="field" style="left:255px;top:145px;width:175px">Last Name</div>
    <div class="field" style="left:40px;top:198px;width:175px">Email Address</div>
    <div class="field" style="left:255px;top:198px;width:175px">Phone</div>
    <div class="field" style="left:40px;top:251px;width:175px">Dealership Name</div>
    <div class="signup">SIGN UP</div>
    <div class="privacy">We respect your privacy.</div>
  </div>
  <div class="abs contact-brand">Maple9Tone</div>
  <div class="abs contact-q">Got a question or comment?</div>
  <p class="abs contact-text">We are constantly working to raise the bar on our services. If you have any questions or concerns about your experience, please let us know.</p>
  <div class="abs contact-row" style="top:257px">
    <span class="contact-icon"><svg width="20" height="16" viewBox="0 0 20 16"><rect x="1" y="1" width="18" height="14" rx="1" fill="none" stroke="#0ea4dc" stroke-width="2"/><path d="M1 2l9 7 9-7" fill="none" stroke="#0ea4dc" stroke-width="2"/></svg></span>
    Mail Us At : &nbsp;info@larkfieldmedia.com;
  </div>
  <div class="abs contact-row" style="top:325px">
    <span class="contact-icon"><svg width="20" height="20" viewBox="0 0 20 20"><path d="M4 2l4 4-2 3q2 4 5 5l3-2 4 4-3 3Q8 18 2 5z" fill="none" stroke="#0ea4dc" stroke-width="2" stroke-linejoin="round"/></svg></span>
    Call Us At : 303 555 0147
  </div>
</section>

<footer class="site-footer">
  <div class="abs copyright">Copyright © 2016 Maple9Tone. All Right Reserved</div>
  <div class="abs social"><i></i><i></i><i></i><i></i><i></i></div>
</footer>

</body>
</html>
```